Business Card Design

We are a law firm which provides services to creditors.....we do collection litigation. I am wide open on suggestions. I was thinking of a square card? Alternatively, a vertically oriented standard card or a folded card.....something unique. I would like to use my firm logo and beyond that, I am open for any and all suggestions. I'm uncertain if the complete log is uploaded? If not, please let me email it to you.

Industry/Entity Type

Law Firm

Contact Information for Business Card

Hart, Crane & Dobbs, P.C.
Tom Dobbs, Lawyer
4387 N Larkspur Ave
Oklahoma City, OK 73924
tdobbs@HcdCounsel.com
www.HcdCounsel.com
mobile: 405-382-7914

```html
<!DOCTYPE html>
<html lang="en">
<head>
<meta charset="utf-8">
<title>Hart, Crane &amp; Dobbs, P.C. — Business Card</title>
<link rel="stylesheet" href="https://fonts.googleapis.com/css2?family=Arimo:wght@400;700&display=swap">
<style>
  :root {
    --page: #efe9df;
    --card: #ffffff;
    --green: #0b5a32;
    --ink: #2e2e2e;
    --gold: #c9a23c;
    --shadow: rgba(0, 0, 0, 0.28);
  }
  * { box-sizing: border-box; margin: 0; padding: 0; }
  html, body {
    width: 1189px;
    height: 1200px;
    overflow: hidden;
    background: var(--page);
    font-family: "Arimo", Arial, sans-serif;
  }
  .canvas { position: relative; width: 1189px; height: 1200px; }

  .card {
    position: absolute;
    left: 171px;
    width: 856px;
    height: 488px;
    background: var(--card);
    border-radius: 20px;
    box-shadow: 6px 8px 14px var(--shadow);
  }
  .card--front { top: 67px; }
  .card--back  { top: 627px; }

  /* firm mark placeholder: plain circle + name */
  .mark {
    position: absolute;
    display: flex;
    flex-direction: column;
    align-items: center;
    gap: 14px;
    width: 260px;
  }
  .mark__dot {
    width: 110px;
    height: 110px;
    border-radius: 50%;
    background: var(--gold);
  }
  .mark__name {
    font-weight: 700;
    font-size: 22px;
    color: var(--green);
    white-space: nowrap;
  }
  .card--front .mark { left: 298px; top: 96px; }
  .card--back .mark  { left: 78px;  top: 136px; }

  .firm-name {
    position: absolute;
    font-weight: 700;
    font-size: 28px;
    white-space: nowrap;
    transform: translateX(-50%);
  }
  .card--front .firm-name { left: 428px; top: 302px; color: var(--green); }
  .card--back .firm-name  { left: 208px; top: 343px; color: var(--ink); }

  .web-rule {
    position: absolute;
    left: 202px;
    top: 383px;
    width: 455px;
    display: flex;
    align-items: center;
    justify-content: space-between;
  }
  .web-rule__line {
    width: 104px;
    height: 2px;
    background: linear-gradient(to right, transparent, var(--green));
  }
  .web-rule__line--right { background: linear-gradient(to left, transparent, var(--green)); }
  .web-rule__url { font-size: 23px; color: var(--green); }

  .divider {
    position: absolute;
    left: 419px;
    top: 67px;
    width: 2px;
    height: 355px;
    background: var(--green);
  }

  .person { position: absolute; left: 471px; top: 80px; }
  .person__name {
    font-weight: 700;
    font-size: 50px;
    line-height: 1;
    color: var(--green);
    letter-spacing: 0.5px;
  }
  .person__title {
    font-weight: 700;
    font-size: 32px;
    line-height: 1;
    margin-top: 6px;
    color: var(--ink);
  }

  .address {
    position: absolute;
    left: 472px;
    top: 220px;
    font-size: 24px;
    line-height: 29px;
    color: var(--ink);
    font-style: normal;
  }

  .contacts {
    position: absolute;
    left: 473px;
    top: 307px;
    list-style: none;
  }
  .contacts__item {
    display: flex;
    align-items: center;
    gap: 13px;
    height: 27.5px;
    font-size: 24px;
    color: var(--ink);
  }
  .contacts__icon { width: 21px; height: 21px; flex: none; }
</style>
</head>
<body>
<div class="canvas">

  <section class="card card--front">
    <div class="mark">
      <span class="mark__dot"></span>
      <span class="mark__name">Hart, Crane &amp; Dobbs</span>
    </div>
    <h1 class="firm-name">Hart, Crane &amp; Dobbs, P.C.</h1>
    <div class="web-rule">
      <span class="web-rule__line"></span>
      <span class="web-rule__url">www.HcdCounsel.com</span>
      <span class="web-rule__line web-rule__line--right"></span>
    </div>
  </section>

  <section class="card card--back">
    <div class="mark">
      <span class="mark__dot"></span>
      <span class="mark__name">Hart, Crane &amp; Dobbs</span>
    </div>
    <h2 class="firm-name">Hart, Crane &amp; Dobbs, P.C.</h2>

    <span class="divider"></span>

    <div class="person">
      <p class="person__name">Tom Dobbs</p>
      <p class="person__title">Lawyer</p>
    </div>

    <address class="address">
      4387 N Larkspur Ave<br>
      Oklahoma City, OK 73924
    </address>

    <ul class="contacts">
      <li class="contacts__item">
        <svg class="contacts__icon" viewBox="0 0 21 21" aria-hidden="true">
          <rect width="21" height="21" rx="3" fill="var(--green)"/>
          <rect x="7" y="3" width="7" height="15" rx="1.5" fill="none" stroke="#fff" stroke-width="1.5"/>
          <rect x="8.5" y="5.5" width="4" height="5" fill="#fff"/>
        </svg>
        405-382-7914
      </li>
      <li class="contacts__item">
        <svg class="contacts__icon" viewBox="0 0 21 21" aria-hidden="true">
          <rect width="21" height="21" rx="3" fill="var(--green)"/>
          <rect x="4" y="6" width="13" height="9" fill="none" stroke="#fff" stroke-width="1.4"/>
          <path d="M4 6 L10.5 11 L17 6 M4 15 L9 10.5 M17 15 L12 10.5" fill="none" stroke="#fff" stroke-width="1.2"/>
        </svg>
        tdobbs@HcdCounsel.com
      </li>
      <li class="contacts__item">
        <svg class="contacts__icon" viewBox="0 0 21 21" aria-hidden="true">
          <rect width="21" height="21" rx="3" fill="var(--green)"/>
          <circle cx="10.5" cy="10.5" r="6.5" fill="none" stroke="#fff" stroke-width="1.3"/>
          <ellipse cx="10.5" cy="10.5" rx="3" ry="6.5" fill="none" stroke="#fff" stroke-width="1.1"/>
          <path d="M4 10.5 H17 M5 7 H16 M5 14 H16" stroke="#fff" stroke-width="1.1"/>
        </svg>
        www.HcdCounsel.com
      </li>
    </ul>
  </section>

</div>
</body>
</html>
```